Accountancy firm needs clean and simple website and optional logo

We need a logo and basic wordpress website design for a Sydney based accountancy firm.
We need a clean and simple logo and website, based on the accounting/finance/tax industry. Simple, credible and official colors.
The logo is expected to be so simple that we have combined into the one job.
If you submit a logo design and we choose it along with someone else's website design you will be paid a bonus of $60. The website design will still win the competition as per normal.
Current website is old and terrible but gives you an idea of the sitemap (super simple) and what they do: www.brookfiscal.com.au
We want original different to normal template looking designs.
We like videos, and like http://www.merivane.com.au/
Feel free to go to clipvault9 and use some videos from there.
We are based in Sydney Australia and in the field of taxation and accounting
We want a clean, formal, credible site, limited pages.
The project is guaranteed, so go for it.
Logo Text
Brook & Associates

```html
<!DOCTYPE html>
<html lang="en">
<head>
<meta charset="utf-8">
<title>Brook &amp; Associates — Tax Accountants</title>
<link href="https://fonts.googleapis.com/css2?family=Fira+Sans+Condensed:wght@400;500&family=Roboto:wght@400;500;700&display=swap" rel="stylesheet">
<style>
:root{
  --blue:#0a87d2;
  --blue-dark:#0068b0;
  --ink:#1f2228;
  --text:#3a3d42;
  --muted:#8a8d92;
  --rule:#d9dadc;
  --grey-band:#e9e9ea;
  --white:#ffffff;
  --footer:#111317;
}
*{box-sizing:border-box;margin:0;padding:0}
html,body{width:720px;height:1200px;overflow:hidden;background:var(--white)}
body{position:relative;font-family:"Roboto",Arial,sans-serif;color:var(--text)}
.abs{position:absolute}
.heading{font-family:"Fira Sans Condensed","Arial Narrow",sans-serif;font-weight:400;color:var(--ink);text-align:center;letter-spacing:.3px}

/* header */
.site-header{left:0;top:0;width:720px;height:62px;background:var(--white);border-bottom:1px solid #e2e2e2}
.brand{left:66px;top:24px;display:flex;align-items:center;gap:7px}
.brand-square{width:14px;height:14px;background:var(--blue)}
.brand-name{font-size:10px;font-weight:700;color:var(--ink);letter-spacing:.2px;line-height:1}
.brand-tag{left:87px;top:36px;font-size:6px;color:var(--text)}
.nav{left:428px;top:34px;height:28px;display:flex;font-size:7px;font-weight:500;color:var(--ink)}
.nav a{display:flex;align-items:center;justify-content:center;color:inherit;text-decoration:none;height:28px}
.nav .active{background:var(--blue);color:var(--white);width:51px}
.nav .about{width:70px}
.nav .services{width:58px}
.nav .contact{width:68px}

/* hero */
.hero{left:0;top:62px;width:720px;height:361px;background:linear-gradient(120deg,#2b3a4c 0%,#4d6a88 35%,#9fb8cf 60%,#c9d7e4 80%,#6b7f93 100%)}
.hero-arrow{width:31px;height:30px;background:rgba(10,12,16,.85);display:flex;align-items:center;justify-content:center}
.hero-caption{left:67px;top:308px;width:376px;height:62px;background:rgba(35,37,40,.82);display:flex;align-items:center;padding-left:25px}
.hero-caption h1{font-family:"Fira Sans Condensed","Arial Narrow",sans-serif;font-weight:400;font-size:17.5px;color:var(--white);letter-spacing:.6px}

/* welcome */
.welcome-title{left:0;top:453px;width:720px;font-size:16px}
.lead{left:0;top:478px;width:720px;text-align:center;font-size:8.4px;color:var(--text)}
.intro{left:70px;top:495px;width:580px;text-align:center;font-size:6.3px;line-height:15.5px;color:var(--muted)}

.feature{width:180px;text-align:center}
.feature svg{display:block;margin:0 auto}
.feature h3{font-family:"Fira Sans Condensed","Arial Narrow",sans-serif;font-weight:400;font-size:10.5px;color:var(--ink);margin-top:9px;letter-spacing:.3px}
.feature p{font-size:6.3px;line-height:15.4px;color:var(--muted);margin-top:4px}
.feature .more{display:block;font-family:"Fira Sans Condensed","Arial Narrow",sans-serif;font-size:8px;color:var(--blue);margin-top:1px;letter-spacing:.3px}
.divider{width:1px;height:116px;background:var(--rule);top:574px}

/* services */
.services-band{left:0;top:725px;width:720px;height:219px;background:var(--grey-band)}
.contact-band{left:0;top:944px;width:720px;height:210px;background:linear-gradient(180deg,#2c3035 0%,#1d2024 55%,#262a2f 100%)}
.services-title{left:0;top:747px;width:720px;font-size:16px}
.services-text{left:80px;top:771px;width:560px;text-align:center;font-size:6.4px;line-height:15.5px;color:var(--muted)}
.card{top:814px;width:135px;height:176px;background:var(--white);padding:8px 7px 0}
.card-photo{width:121px;height:76px}
.card h4{font-size:7.6px;font-weight:500;color:var(--ink);margin-top:9px}
.card p{font-size:6.2px;line-height:15.4px;color:var(--muted);margin-top:2px}
.card .more{display:flex;align-items:center;gap:2px;font-size:6.6px;font-weight:500;color:var(--blue);margin-top:1px}
.round-arrow{width:21px;height:21px;border-radius:50%;background:var(--white);box-shadow:0 0 3px rgba(0,0,0,.15);display:flex;align-items:center;justify-content:center}

/* contact */
.contact-title{left:0;top:1025px;width:720px;font-size:16.5px;color:var(--white)}
.contact-text{left:80px;top:1047px;width:560px;text-align:center;font-size:6.8px;line-height:15.5px;color:var(--white)}
.cta{left:308px;top:1085px;width:104px;height:36px;background:var(--blue);color:var(--white);font-size:8.5px;font-weight:500;letter-spacing:.4px;display:flex;align-items:center;justify-content:center;text-decoration:none}

/* footer */
.site-footer{left:0;top:1154px;width:720px;height:46px;background:var(--footer)}
.copyright{left:66px;top:1173px;font-size:6.6px;color:#9a9da2}
.social{top:1169px;left:578px;display:flex;gap:3.5px}
.social span{width:16px;height:16px;border-radius:50%;background:#5d6168}
</style>
</head>
<body>

<header class="site-header abs">
  <div class="brand abs"><span class="brand-square"></span><span class="brand-name">BROOK &amp; ASSOCIATES</span></div>
  <div class="brand-tag abs">tax accountants</div>
  <nav class="nav abs">
    <a class="active" href="#">HOME</a>
    <a class="about" href="#">ABOUT</a>
    <a class="services" href="#">SERVICES</a>
    <a class="contact" href="#">CONTACT</a>
  </nav>
</header>

<section class="hero abs" role="img" aria-label="Photo of business people reviewing bar charts on a tablet over paper reports"></section>
<a class="hero-arrow abs" style="left:18px;top:234px" href="#" aria-label="Previous slide">
  <svg width="10" height="12" viewBox="0 0 10 12"><path d="M7 1 2 6l5 5" fill="none" stroke="#fff" stroke-width="1.3"/></svg>
</a>
<a class="hero-arrow abs" style="left:674px;top:234px" href="#" aria-label="Next slide">
  <svg width="10" height="12" viewBox="0 0 10 12"><path d="M3 1l5 5-5 5" fill="none" stroke="#fff" stroke-width="1.3"/></svg>
</a>
<div class="hero-caption abs"><h1>TAKE THE WORRY OUT OF TAX AND BUSINESS</h1></div>

<h2 class="heading welcome-title abs">WELCOME TO BROOK &amp; ASSOCIATES</h2>
<p class="lead abs">Ut wisi enim ad minim veniam, quis nostrud exerci tation ullamcorper suscipit lobortis nisl ut aliquip ex ea commodo consequa</p>
<p class="intro abs">Lorem ipsum dolor sit amet, consectetuer adipiscing elit, sed diam nonummy nibh euismod tincidunt ut laoreet dolore magna aliquam erat volutpat. Ut wisi enim ad minim veniam, quis nostrud exerci tation ullamcorper suscipit lobortis nisl ut aliquip ex ea commodo consequat. Duis autem vel eum iriure dolor in hendrerit in vulputate velit esse molestie consequat, vel illum dolore eu feugiat nulla facilisis at vero eros et accumsan et iusto odio dignissim qui blandit praesent luptatum zzril delenit augue duis dolore te feugait nulla facilisi.</p>

<div class="feature abs" style="left:73px;top:562px">
  <svg width="32" height="32" viewBox="0 0 32 32"><path d="M3 1h12l5 5v22H3z" fill="var(--blue)"/><path d="M11 7h11l7 7v17H11z" fill="#fff" stroke="var(--blue)" stroke-width="2.4"/><path d="M22 7v7h7" fill="none" stroke="var(--blue)" stroke-width="2.4"/></svg>
  <h3>ACCOUNTING</h3>
  <p>Pellentesque tristique justo eget libero lacinia pretium. Etiam imperdiet tempus est, et maximus quam vehicula id. Nullam urna libero, ornare nec eleifend in, mattis nec eros. Pellentesque ornare ante mauris.</p>
  <span class="more">READ MORE</span>
</div>
<div class="divider abs" style="left:266px"></div>
<div class="feature abs" style="left:274px;top:562px">
  <svg width="34" height="32" viewBox="0 0 34 32"><rect x="1.5" y="6" width="31" height="21" fill="none" stroke="var(--blue)" stroke-width="3"/><circle cx="17" cy="16.5" r="6.5" fill="var(--blue)"/><path d="M15.5 13.5l2-1.2v8.5" fill="none" stroke="#fff" stroke-width="1.6"/><rect x="5" y="10" width="3" height="3" fill="var(--blue)"/><rect x="26" y="20" width="3" height="3" fill="var(--blue)"/></svg>
  <h3>FINANCE</h3>
  <p>Cras nulla massa, facilisis id tortor sit amet, bibendum sodales urna. Phasellus nulla sapien, congue ut neque eget, blandit volutpat sem. Donec facilisis lorem ex, eu volutpat velit iaculis eu.</p>
  <span class="more">READ MORE</span>
</div>
<div class="divider abs" style="left:459px"></div>
<div class="feature abs" style="left:475px;top:562px">
  <svg width="24" height="32" viewBox="0 0 24 32"><path d="M12 1v30" stroke="var(--blue)" stroke-width="2.6"/><path d="M20 9c-1-3-4-4-8-4s-7 2-7 5.5c0 8 15 4 15 12 0 3.5-3 5.5-8 5.5s-7.5-2-8.5-5" fill="none" stroke="var(--blue)" stroke-width="3.4"/></svg>
  <h3>TAX</h3>
  <p>Integer placerat sapien in massa molestie, sed viverra tortor facilisis. Proin non neque vel massa feugiat sodales. Cras id enim dignissim, vulputate nulla sit amet, varius urna. Cras quis dignissim ligula.</p>
  <span class="more">READ MORE</span>
</div>

<section class="services-band abs"></section>
<section class="contact-band abs" role="img" aria-label="Dark photo of colleagues joining hands in a team huddle"></section>

<h2 class="heading services-title abs">OUR SERVICES</h2>
<p class="services-text abs">Duis autem vel eum iriure dolor in hendrerit in vulputate velit esse molestie consequat, vel illum dolore eu feugiat nulla facilisis at vero eros et accumsan et iusto odio dignissim qui blandit praesent luptatum zzril delenit augue duis dolore te feugait nulla facilisi.</p>

<a class="round-arrow abs" style="left:32px;top:877px" href="#" aria-label="Previous services">
  <svg width="8" height="8" viewBox="0 0 8 8"><path d="M4 1 1 4l3 3M7 1 4 4l3 3" fill="none" stroke="#777" stroke-width=".9"/></svg>
</a>
<a class="round-arrow abs" style="left:667px;top:877px" href="#" aria-label="Next services">
  <svg width="8" height="8" viewBox="0 0 8 8"><path d="M1 1l3 3-3 3M4 1l3 3-3 3" fill="none" stroke="#777" stroke-width=".9"/></svg>
</a>

<article class="card abs" style="left:66px">
  <div class="card-photo" role="img" aria-label="Photo of hands typing on a laptop beside printed charts" style="background:linear-gradient(135deg,#f1f2f3,#c9ccd0 60%,#8d9298)"></div>
  <h4>Tax Planning and Returns</h4>
  <p>Lorem ipsum dolor sit amet, conse ctetuer adipiscing elit, sed diam nonummy nibh euismod.</p>
  <span class="more">Read More <svg width="7" height="7" viewBox="0 0 8 8"><circle cx="4" cy="4" r="4" fill="var(--blue)"/><path d="M3.2 2.2 5 4 3.2 5.8" fill="none" stroke="#fff" stroke-width="1.1"/></svg></span>
</article>
<article class="card abs" style="left:217px">
  <div class="card-photo" role="img" aria-label="Photo of a busy desk with papers, tablet and coffee" style="background:linear-gradient(135deg,#6a7b6a,#b08a55 45%,#4f6f8c)"></div>
  <h4>Litigation Assistance</h4>
  <p>Lorem ipsum dolor sit amet, conse ctetuer adipiscing elit, sed diam nonummy nibh euismod.</p>
  <span class="more">Read More <svg width="7" height="7" viewBox="0 0 8 8"><circle cx="4" cy="4" r="4" fill="var(--blue)"/><path d="M3.2 2.2 5 4 3.2 5.8" fill="none" stroke="#fff" stroke-width="1.1"/></svg></span>
</article>
<article class="card abs" style="left:368px">
  <div class="card-photo" role="img" aria-label="Photo of a person working with a calculator at a white desk" style="background:linear-gradient(135deg,#7a6a60,#d6d6d6 50%,#f0f0f0)"></div>
  <h4>Asset Protection Services</h4>
  <p>Lorem ipsum dolor sit amet, conse ctetuer adipiscing elit, sed diam nonummy nibh euismod.</p>
  <span class="more">Read More <svg width="7" height="7" viewBox="0 0 8 8"><circle cx="4" cy="4" r="4" fill="var(--blue)"/><path d="M3.2 2.2 5 4 3.2 5.8" fill="none" stroke="#fff" stroke-width="1.1"/></svg></span>
</article>
<article class="card abs" style="left:518px">
  <div class="card-photo" role="img" aria-label="Photo of a business handshake in front of office towers" style="background:linear-gradient(180deg,#3c6fb0,#7fa7d6 55%,#4a4f57)"></div>
  <h4>Business Setup</h4>
  <p>Lorem ipsum dolor sit amet, conse ctetuer adipiscing elit, sed diam nonummy nibh euismod.</p>
  <span class="more">Read More <svg width="7" height="7" viewBox="0 0 8 8"><circle cx="4" cy="4" r="4" fill="var(--blue)"/><path d="M3.2 2.2 5 4 3.2 5.8" fill="none" stroke="#fff" stroke-width="1.1"/></svg></span>
</article>

<h2 class="heading contact-title abs">CONTACT NOW</h2>
<p class="contact-text abs">Duis autem vel eum iriure dolor in hendrerit in vulputate velit esse molestie consequat, vel illum dolore eu feugiat nulla facilisis at vero eros et accumsan et iusto odio dignissim qui blandit praesent luptatum zzril delenit augue duis dolore te feugait nulla facilisi.</p>
<a class="cta abs" href="#">CLICK HERE</a>

<footer class="site-footer abs"></footer>
<p class="copyright abs">Copyright © 2015 Brook &amp; Associates. All rights reserved.</p>
<div class="social abs" aria-label="Social links"><span></span><span></span><span></span><span></span></div>

</body>
</html>
```